Computer consultant business card

Bexil Software is a newly started computer consulting company. It's a small one-man company that provides mostly Vornix applications but also websites in collaboration with designers. I'm running this company on the side of full time university studies.

I want the final design to be clean and memorable. Be creative! :)

Some inspiration:
http://www.pixelmarta.com/design/48317
http://www.pixelmarta.com/design/2739164/business-card-design-by-frostlynk
http://www.pixelmarta.com/design/604281/business-card-design-by-koralind-vestrabanu

See attachment for my company logo.
Updates

I would like to thank everyone for submitting! I'll need a couple of days to review and ultimately select a design.

Target Market(s)

Non-technical entrepreneurs and small companies.

Industry/Entity Type

University

Requirements
Must have
• My company logo.
In any way, both colors from my logo.
First- and last name, e-mail and phone number.
Double-sided design.
Nice to have
• Something creative with the symbol in my logo

```html
<!DOCTYPE html>
<html lang="en">
<head>
<meta charset="utf-8">
<title>Trenvaq Software – Business Card</title>
<link rel="stylesheet" href="https://fonts.googleapis.com/css2?family=Mulish:wght@400;700&family=Quicksand:wght@600&family=Arimo:wght@400&display=swap">
<style>
  :root {
    --backdrop: #b48f62;
    --card-white: #ffffff;
    --ink: #2f2d2e;
    --brand-blue: #4673b9;
    --label-ink: #1e1a16;
    --muted: #4a4a4a;
    --deep-black: #050505;
    --slate: #2f3139;
    --slate-blue: #4b5b80;
  }
  * { box-sizing: border-box; margin: 0; padding: 0; }
  html, body {
    width: 1200px; height: 788px; overflow: hidden;
    background: var(--backdrop);
    font-family: "Mulish", sans-serif;
  }
  .sheet { position: relative; width: 1200px; height: 788px; }

  .view-label {
    position: absolute; width: 300px; text-align: center;
    font-family: "Arimo", sans-serif;
    font-size: 20px; font-weight: 400; color: var(--label-ink);
  }
  .label-front  { left: 170px; top: 34px; }
  .label-back-1 { left: 745px; top: 34px; }
  .label-back-2 { left: 170px; top: 405px; }
  .label-back-3 { left: 745px; top: 405px; }

  .card {
    position: absolute; width: 526px; height: 299px;
    border-radius: 22px; overflow: hidden;
    background: var(--card-white);
    box-shadow: 0 3px 8px rgba(0,0,0,0.35);
  }
  .card-front  { left: 55px;  top: 75px; }
  .card-back-1 { left: 622px; top: 75px; }
  .card-back-2 { left: 53px;  top: 446px; background: var(--deep-black); }
  .card-back-3 {
    left: 622px; top: 446px;
    background: radial-gradient(ellipse at 60% 95%, var(--slate-blue) 0%, var(--slate) 75%);
  }

  .brand-mark {
    position: absolute; display: flex; align-items: center; gap: 20px;
    left: 0; right: 0; justify-content: center;
  }
  .brand-dot { border-radius: 50%; background: var(--brand-blue); flex: none; }
  .brand-name {
    font-family: "Quicksand", sans-serif;
    font-weight: 600; color: var(--ink); line-height: 1;
  }
  .on-dark .brand-name { color: var(--card-white); }

  .card-front .brand-mark { top: 34px; height: 82px; }
  .card-front .brand-dot { width: 82px; height: 82px; }
  .card-front .brand-name { font-size: 56px; }

  .card-back .brand-mark { top: 90px; height: 106px; }
  .card-back .brand-dot { width: 106px; height: 106px; }
  .card-back .brand-name { font-size: 72px; }

  .holder { position: absolute; top: 165px; left: 0; right: 0; text-align: center; }
  .holder-name { font-size: 18px; font-weight: 700; color: var(--ink); line-height: 22px; }
  .holder-role { font-size: 13px; color: var(--muted); line-height: 16px; }

  .footer-bands { position: absolute; left: 0; bottom: 0; width: 526px; height: 52px; }
  .contact {
    position: absolute; left: 311px; top: 256px;
    color: var(--card-white); font-size: 13.5px; line-height: 18px;
  }
  .contact b { font-style: italic; font-weight: 700; }

  .web-address {
    position: absolute; left: 0; right: 0; top: 248px; text-align: center;
    font-size: 18px; font-weight: 400; letter-spacing: 4.5px; color: var(--ink);
  }
  .on-dark .web-address { color: var(--card-white); top: 254px; }

  .texture {
    position: absolute; inset: 0;
    background:
      radial-gradient(ellipse 190px 140px at 22% 10%, rgba(120,120,130,0.45), transparent 70%),
      radial-gradient(ellipse 170px 140px at 78% 92%, rgba(140,130,140,0.45), transparent 70%);
  }
</style>
</head>
<body>
<main class="sheet">
  <div class="view-label label-front">Front</div>
  <div class="view-label label-back-1">Back - 1</div>
  <div class="view-label label-back-2">Back - 2</div>
  <div class="view-label label-back-3">Back - 3</div>

  <section class="card card-front">
    <div class="brand-mark">
      <span class="brand-dot"></span>
      <span class="brand-name">trenvaq</span>
    </div>
    <div class="holder">
      <p class="holder-name">First Name Last Name</p>
      <p class="holder-role">Designation</p>
    </div>
    <svg class="footer-bands" viewBox="0 0 526 52" aria-hidden="true">
      <polygon points="0,25 262,25 252,35 0,35" fill="var(--ink)"/>
      <polygon points="0,42 248,42 284,0 526,0 526,52 0,52" fill="var(--brand-blue)"/>
      <polygon points="0,35 252,35 248,42 0,42" fill="var(--card-white)"/>
    </svg>
    <p class="contact"><b>p</b> : +12 345 6789<br><b>e</b> : info@trenvaqsoft.net</p>
  </section>

  <section class="card card-back card-back-1">
    <div class="brand-mark">
      <span class="brand-dot"></span>
      <span class="brand-name">trenvaq</span>
    </div>
    <p class="web-address">www.trenvaqsoft.net</p>
  </section>

  <section class="card card-back card-back-2 on-dark">
    <div class="texture" role="img" aria-label="Soft perforated metal texture glowing in two corners"></div>
    <div class="brand-mark">
      <span class="brand-dot"></span>
      <span class="brand-name">trenvaq</span>
    </div>
    <p class="web-address">www.trenvaqsoft.net</p>
  </section>

  <section class="card card-back card-back-3 on-dark">
    <div class="brand-mark">
      <span class="brand-dot"></span>
      <span class="brand-name">trenvaq</span>
    </div>
    <p class="web-address">www.trenvaqsoft.net</p>
  </section>
</main>
</body>
</html>
```